Need Business Card for our Real Estate Business with Sales Executive's Picture

PANTONE 484 C ( RED)

PANTONE 2766 C ( BLUE

Industry/Entity Type

Real Estate

Contact Information for Business Card

Name, Mobile, email, & picture of Person
Agency Phone, address, Web address

Requirements
Must have
• Our Logo Colours, Agent Picture,

```html
<!DOCTYPE html>
<html lang="en">
<head>
<meta charset="utf-8">
<title>Dunmore Real Estate – Business Card</title>
<link href="https://fonts.googleapis.com/css2?family=Roboto:wght@400;500;700&display=swap" rel="stylesheet">
<style>
  :root {
    --maroon: #5e0a13;
    --navy: #0c1a44;
    --paper: #f3f3f3;
    --white: #ffffff;
    --backdrop: #e6e2dc;
    --photo-dark: #14245a;
    --photo-light: #2c4a96;
  }
  * { margin: 0; padding: 0; box-sizing: border-box; }
  html, body { width: 1200px; height: 960px; overflow: hidden; }
  body { background: var(--backdrop); font-family: 'Roboto', Arial, sans-serif; }
  .stage { position: relative; width: 1200px; height: 960px; }

  .card { position: absolute; width: 600px; height: 343px; overflow: hidden; }
  .card-front { left: 314px; top: 113px; background: var(--paper); }
  .card-back { left: 311px; top: 472px; background: var(--navy); }

  .front-band { position: absolute; left: 0; top: 0; width: 600px; height: 343px; }

  .brand { position: absolute; left: 0; right: 0; text-align: center; color: var(--navy); font-weight: 500; }
  .brand-front { top: 128px; font-size: 30px; letter-spacing: 3px; }
  .brand-front .brand-sub { display: block; font-size: 11px; letter-spacing: 2px; margin-top: 4px; }
  .brand-mark { display: inline-block; width: 12px; height: 12px; background: currentColor; margin-right: 10px; vertical-align: 4px; }

  .person { position: absolute; left: 35px; top: 241px; color: var(--white); }
  .person-name { font-size: 20px; font-weight: 500; letter-spacing: 0.3px; }
  .person-role { font-size: 15px; margin-top: 6px; }
  .person-address { font-size: 14px; line-height: 19px; margin-top: 7px; }

  .contacts { position: absolute; right: 28px; top: 247px; list-style: none; color: var(--white); font-size: 14px; }
  .contacts li { display: flex; justify-content: flex-end; align-items: center; height: 19.5px; }
  .contacts svg { width: 13px; height: 13px; margin-left: 8px; fill: var(--white); }

  .portrait { position: absolute; left: 18px; top: 12px; width: 242px; height: 331px;
    background: radial-gradient(ellipse at 50% 30%, var(--photo-light), var(--photo-dark) 75%); border-radius: 90px 90px 0 0; }

  .brand-back { position: absolute; left: 318px; width: 260px; top: 232px; text-align: center; color: var(--white); font-weight: 500; }
  .brand-back .brand-name { font-size: 34px; letter-spacing: 3px; }
  .brand-back .brand-sub { display: block; font-size: 11px; letter-spacing: 2px; margin-top: 4px; }
  .brand-back .brand-rule { height: 1px; background: var(--white); margin: 6px 14px; }
  .brand-web { font-size: 14px; letter-spacing: 4.5px; margin-top: 6px; }
</style>
</head>
<body>
<main class="stage">

  <section class="card card-front" aria-label="Business card front">
    <svg class="front-band" viewBox="0 0 600 343" aria-hidden="true">
      <polygon points="0,209 600,209 600,343 0,343" fill="var(--maroon)"/>
      <polyline points="0,203 80,203 102,220 124,203 600,203" fill="none" stroke="var(--navy)" stroke-width="3"/>
      <polyline points="0,208 78,208 102,227 126,208 600,208" fill="none" stroke="var(--navy)" stroke-width="2"/>
      <rect x="98" y="202" width="7" height="7" fill="var(--maroon)"/>
    </svg>

    <div class="brand brand-front">
      <span class="brand-mark"></span>DUNMORE
      <span class="brand-sub">REAL ESTATE</span>
    </div>

    <div class="person">
      <p class="person-name">DANIEL REYES</p>
      <p class="person-role">CEO/FOUNDER</p>
      <p class="person-address">4216 Willow Bend<br>Juneau, Alaska 99801</p>
    </div>

    <ul class="contacts">
      <li>512 380 7741
        <svg viewBox="0 0 24 24"><path d="M6.6 10.8a15 15 0 0 0 6.6 6.6l2.2-2.2a1 1 0 0 1 1-.25 11.4 11.4 0 0 0 3.6.57 1 1 0 0 1 1 1V20a1 1 0 0 1-1 1A17 17 0 0 1 3 4a1 1 0 0 1 1-1h3.5a1 1 0 0 1 1 1c0 1.25.2 2.45.57 3.57a1 1 0 0 1-.25 1z"/></svg>
      </li>
      <li>512 906 2275
        <svg viewBox="0 0 24 24"><path d="M7 1h10a2 2 0 0 1 2 2v18a2 2 0 0 1-2 2H7a2 2 0 0 1-2-2V3a2 2 0 0 1 2-2zm0 3v14h10V4zm5 15.5a1 1 0 1 0 0 2 1 1 0 0 0 0-2z"/></svg>
      </li>
      <li>dan@dunmore.com
        <svg viewBox="0 0 24 24"><path d="M2 5h20v14H2zm2 2v.5l8 5 8-5V7zm0 3v7h16v-7l-8 5z"/></svg>
      </li>
      <li>www.dunmore.com
        <svg viewBox="0 0 24 24"><circle cx="12" cy="12" r="10"/></svg>
      </li>
    </ul>
  </section>

  <section class="card card-back" aria-label="Business card back">
    <div class="portrait" role="img" aria-label="Portrait photo of the sales executive in a blue suit"></div>

    <div class="brand-back">
      <p class="brand-name"><span class="brand-mark"></span>DUNMORE</p>
      <div class="brand-rule"></div>
      <span class="brand-sub">REAL ESTATE</span>
      <div class="brand-rule"></div>
      <p class="brand-web">www.dunmore.com</p>
    </div>
  </section>

</main>
</body>
</html>
```